Need a redesign for our Wordpress Credit report website

Hi, We need someone to redesign our Wordpress credit report website, lumenledger.co.za. The designer will be responsible for the following pages:
- home page
- blog page
- single post
- dashboard
- credit report page

About LumenLedger.co.za
Lumen Ledger is a consumer focussed credit report platform where South African citizens can get an easy to understand credit report that shows them where to improve their credit scores.

```html
<!DOCTYPE html>
<html lang="en">
<head>
<meta charset="utf-8">
<title>Lumen Ledger – Check your credit score</title>
<link href="https://fonts.googleapis.com/css2?family=Montserrat:wght@500;600;700;800&family=Open+Sans:wght@400;600;700&display=swap" rel="stylesheet">
<style>
:root{
  --blue:#1b6fb5;
  --blue-dark:#14508a;
  --green:#8cc63f;
  --navy:#1d2b4c;
  --ink:#2b2f36;
  --muted:#6b7280;
  --line:#cfd8e3;
  --soft:#f1f3f6;
  --white:#ffffff;
  --hero-art-a:#fde3e3;
  --hero-art-b:#e3f0fb;
}
*{box-sizing:border-box;margin:0;padding:0}
html,body{width:1200px;height:2700px;overflow:hidden}
body{font-family:"Open Sans",Arial,sans-serif;color:var(--ink);background:var(--white);position:relative}
.head-font{font-family:"Montserrat",Arial,sans-serif}

/* header */
.site-header{position:absolute;top:0;left:0;width:1200px;height:80px;display:flex;align-items:center;justify-content:space-between;padding:0 40px;border-bottom:1px solid #eef1f5}
.brand{display:flex;align-items:center;gap:10px;font-family:"Montserrat",sans-serif;font-weight:800;font-size:24px;color:var(--blue);text-decoration:none}
.brand-dot{width:34px;height:34px;border-radius:50%;background:var(--green)}
.main-nav{display:flex;align-items:center;gap:34px;font-family:"Montserrat",sans-serif;font-size:15px;font-weight:600;color:var(--ink)}
.main-nav a{color:inherit;text-decoration:none}
.main-nav .is-active{color:var(--blue);border-bottom:2px solid var(--blue);padding-bottom:4px}
.btn-login{background:var(--green);color:#fff !important;padding:8px 22px;border-radius:20px}

/* section titles */
.section-title{position:absolute;left:0;width:1200px;text-align:center;font-family:"Montserrat",sans-serif;font-weight:800;font-size:34px;color:var(--blue);letter-spacing:.5px}
.section-title .accent{color:var(--green)}
.section-title::after{content:"";display:block;width:90px;height:3px;background:var(--green);margin:12px auto 0}

/* hero */
.hero-title{top:100px;font-size:38px}
.signup-card{position:absolute;left:40px;top:190px;width:330px;border:1px solid var(--line);background:#fff;box-shadow:0 6px 18px rgba(20,40,80,.08)}
.signup-card h2{background:var(--navy);color:#fff;font-family:"Montserrat",sans-serif;font-size:19px;font-weight:700;padding:22px 26px}
.signup-form{padding:22px 26px 24px}
.field{display:block;width:100%;height:40px;border:1px solid var(--line);margin-bottom:14px;padding:0 12px;font-size:13px;color:var(--muted);line-height:40px}
.agree{display:flex;align-items:center;gap:10px;font-size:12px;color:var(--muted);margin:4px 0 18px}
.agree span.box{width:16px;height:16px;border:1px solid var(--line)}
.btn-primary{display:block;width:100%;height:48px;background:var(--green);color:#fff;font-family:"Montserrat",sans-serif;font-weight:800;font-size:17px;text-align:center;line-height:48px}
.fineprint{font-size:9.5px;color:var(--muted);line-height:1.45;margin-top:14px}
.hero-art{position:absolute;left:470px;top:190px;width:620px;height:520px;border-radius:50%;background:radial-gradient(circle at 50% 50%,var(--hero-art-a) 0%,var(--hero-art-b) 70%,#fff 100%)}
.perk-list{position:absolute;left:520px;top:730px;width:600px;display:grid;grid-template-columns:1fr 1fr;gap:16px 30px;font-size:13px;color:var(--ink);list-style:none}
.perk-list li{display:flex;align-items:center;gap:10px}
.tick{width:18px;height:18px;flex:none}

/* features */
.features-title{top:900px}
.device-art{position:absolute;left:40px;top:1000px;width:480px;height:300px;border-radius:8px;background:linear-gradient(160deg,#e9eef4,#c9d3df)}
.feature-grid{position:absolute;left:570px;top:1020px;width:530px;display:grid;grid-template-columns:repeat(3,1fr);gap:20px}
.feature-box{height:84px;border:1.5px solid #a9c6e6;border-radius:4px;display:flex;align-items:center;gap:10px;padding:0 12px;font-size:12.5px;line-height:1.3}
.feature-box svg{flex:none}
.feature-wide{position:absolute;left:570px;top:1220px;width:530px;height:70px}

/* why us */
.why-title{top:1350px}
.reason-card{position:absolute;top:1440px;width:330px;height:320px;border:1.5px solid #a9c6e6;border-radius:4px;padding:70px 28px 20px;text-align:center}
.reason-card h3{font-family:"Montserrat",sans-serif;font-weight:800;font-size:16px;color:var(--ink);line-height:1.35;margin-bottom:14px}
.reason-card p{font-size:12.5px;color:var(--muted);line-height:1.6}
.reason-icon{position:absolute;top:-30px;left:50%;margin-left:-30px;width:60px;height:60px;border-radius:50%;background:var(--green);display:flex;align-items:center;justify-content:center}

/* testimonials */
.testimonials{position:absolute;top:1870px;left:0;width:1200px;height:560px;background:var(--soft)}
.testi-title{top:1960px}
.testi-card{position:absolute;top:2040px;width:230px;height:300px;background:#fff;padding:26px 20px;text-align:center;box-shadow:0 4px 14px rgba(20,40,80,.06)}
.stars{color:#f5b400;font-size:16px;letter-spacing:2px}
.testi-card p{font-size:12.5px;color:var(--muted);line-height:1.6;margin:14px 0 18px;height:120px}
.avatar{width:46px;height:46px;border-radius:50%;background:linear-gradient(135deg,#c9d3df,#9fb0c4);margin:0 auto 8px}
.testi-name{font-size:12px;font-weight:700;color:var(--ink)}
.carousel-arrow{position:absolute;top:2170px;width:30px;height:30px}

/* footer */
.site-footer{position:absolute;top:2470px;left:0;width:1200px;height:230px}
.footer-brand{position:absolute;left:40px;top:40px}
.footer-col{position:absolute;top:40px;font-size:11.5px;line-height:1.75;color:var(--muted)}
.footer-col h4{font-family:"Montserrat",sans-serif;font-size:13px;font-weight:800;color:var(--blue);margin-bottom:6px}
.social{display:flex;gap:8px;margin-top:6px}
.social span{width:24px;height:24px;border-radius:50%;background:var(--blue)}
.pay-methods{position:absolute;left:40px;top:170px;display:flex;gap:12px}
.pay-methods span{width:52px;height:32px;border-radius:4px;background:#e3e7ed;border:1px solid var(--line)}
.copyright{position:absolute;right:40px;top:180px;font-size:11px;color:var(--muted)}
</style>
</head>
<body>

<header class="site-header">
  <a class="brand" href="#"><span class="brand-dot"></span>Lumen Ledger</a>
  <nav class="main-nav">
    <a class="is-active" href="#">Home</a>
    <a href="#">Articles</a>
    <a href="#">About</a>
    <a href="#">Contact</a>
    <a class="btn-login" href="#">Login</a>
  </nav>
</header>

<h1 class="section-title hero-title">CHECK YOUR CREDIT <span class="accent">SCORE</span> WITHIN SECONDS</h1>

<section class="signup-card">
  <h2>GET STARTED NOW</h2>
  <div class="signup-form">
    <div class="field">ID Number</div>
    <div class="field">First Name</div>
    <div class="field">Last Name</div>
    <div class="field">Primary Email</div>
    <div class="field">Mobile Number</div>
    <div class="agree"><span class="box"></span>I agree with the terms and conditions</div>
    <div class="btn-primary">SHOW MY SCORE</div>
    <p class="fineprint">By signing up and agreeing, you consent to us running a credit check and sharing your results securely. We never share your details with third parties.</p>
  </div>
</section>

<div class="hero-art" role="img" aria-label="Illustration of hands holding a credit report with charts and a credit card"></div>

<ul class="perk-list">
  <li><svg class="tick" viewBox="0 0 18 18"><circle cx="9" cy="9" r="9" fill="#8cc63f"/><path d="M5 9.5l2.6 2.5L13 6.5" stroke="#fff" stroke-width="2" fill="none"/></svg>See your most recent credit score</li>
  <li><svg class="tick" viewBox="0 0 18 18"><circle cx="9" cy="9" r="9" fill="#8cc63f"/><path d="M5 9.5l2.6 2.5L13 6.5" stroke="#fff" stroke-width="2" fill="none"/></svg>Get access to your full credit profile</li>
  <li><svg class="tick" viewBox="0 0 18 18"><circle cx="9" cy="9" r="9" fill="#8cc63f"/><path d="M5 9.5l2.6 2.5L13 6.5" stroke="#fff" stroke-width="2" fill="none"/></svg>See who has been looking at your profile</li>
  <li><svg class="tick" viewBox="0 0 18 18"><circle cx="9" cy="9" r="9" fill="#8cc63f"/><path d="M5 9.5l2.6 2.5L13 6.5" stroke="#fff" stroke-width="2" fill="none"/></svg>See if you have any adverse or Blacklistings</li>
</ul>

<h2 class="section-title features-title">SYSTEM <span class="accent">FEATURES</span></h2>

<div class="device-art" role="img" aria-label="Desktop, tablet and phone showing the credit score dashboard"></div>

<div class="feature-grid">
  <div class="feature-box"><svg width="26" height="26" viewBox="0 0 26 26"><rect x="3" y="5" width="20" height="16" rx="2" fill="none" stroke="#1b6fb5" stroke-width="2"/><path d="M3 10h20" stroke="#1b6fb5" stroke-width="2"/></svg>Budget tool - easily create a budget</div>
  <div class="feature-box"><svg width="26" height="26" viewBox="0 0 26 26"><path d="M4 20l6-7 4 4 8-10" stroke="#1b6fb5" stroke-width="2" fill="none"/></svg>Improve your credit score eBook</div>
  <div class="feature-box"><svg width="26" height="26" viewBox="0 0 26 26"><rect x="5" y="3" width="16" height="20" fill="none" stroke="#1b6fb5" stroke-width="2"/><path d="M9 9h8M9 13h8M9 17h5" stroke="#1b6fb5" stroke-width="2"/></svg>Personal Budgeting Spreadsheet</div>
  <div class="feature-box"><svg width="26" height="26" viewBox="0 0 26 26"><circle cx="13" cy="13" r="10" fill="none" stroke="#1b6fb5" stroke-width="2"/><path d="M11 9l6 4-6 4z" fill="#1b6fb5"/></svg>Perfect score video course</div>
  <div class="feature-box"><svg width="26" height="26" viewBox="0 0 26 26"><rect x="3" y="6" width="20" height="14" rx="2" fill="none" stroke="#1b6fb5" stroke-width="2"/><path d="M11 10l5 3-5 3z" fill="#1b6fb5"/></svg>Personal Finance Video Tutorials</div>
  <div class="feature-box"><svg width="26" height="26" viewBox="0 0 26 26"><path d="M5 15v-3a8 8 0 0116 0v3" fill="none" stroke="#1b6fb5" stroke-width="2"/><rect x="3" y="14" width="5" height="7" rx="1" fill="#1b6fb5"/><rect x="18" y="14" width="5" height="7" rx="1" fill="#1b6fb5"/></svg>Dedicated 24/7 Support</div>
</div>
<div class="feature-box feature-wide"><svg width="26" height="26" viewBox="0 0 26 26"><path d="M6 4h10l4 4v14H6z" fill="none" stroke="#1b6fb5" stroke-width="2"/><path d="M9 14l3 3 5-6" stroke="#8cc63f" stroke-width="2" fill="none"/></svg>Dispute generator - easily manage disputes</div>

<h2 class="section-title why-title">WHY GET YOUR <span class="accent">SCORE</span> FROM US?</h2>

<article class="reason-card" style="left:40px">
  <div class="reason-icon"><svg width="28" height="28" viewBox="0 0 28 28"><path d="M14 3l9 4v6c0 6-4 10-9 12-5-2-9-6-9-12V7z" fill="#fff"/></svg></div>
  <h3>WE DON'T ABUSE YOUR PERSONAL INFORMATION</h3>
  <p>Companies that give out free credit scores use your personal information to sell you financial products. That's how they can afford to give it to you for free. We believe that your personal information should be protected and not abused. That's why we took a small fee. It enables us to protect your information and not abuse it.</p>
</article>
<article class="reason-card" style="left:435px">
  <div class="reason-icon"><svg width="28" height="28" viewBox="0 0 28 28"><rect x="6" y="4" width="16" height="20" rx="1" fill="#fff"/><path d="M10 10h8M10 14h8M10 18h5" stroke="#8cc63f" stroke-width="2"/></svg></div>
  <h3>OUR REPORT IS SUPER EASY TO UNDERSTAND</h3>
  <p>Our credit report is one of the easiest reports to understand. The report is neatly laid out and you will see immediately if you are eligible for finance, if you are blacklisted and where you can improve.</p>
</article>
<article class="reason-card" style="left:830px">
  <div class="reason-icon"><svg width="28" height="28" viewBox="0 0 28 28"><circle cx="10" cy="10" r="4" fill="#fff"/><circle cx="19" cy="10" r="4" fill="#fff"/><path d="M3 23c0-5 3-8 7-8s7 3 7 8zM13 23c0-5 2-8 6-8s6 3 6 8z" fill="#fff"/></svg></div>
  <h3>300,000 + SOUTH AFRICANS HAVE TRUSTED US</h3>
  <p>Since 2006 we have helped over 300,000 South Africans keep track of their credit reports, so you can rest assured knowing that we have a proven track record and that you are in safe hands with us.</p>
</article>

<section class="testimonials"></section>
<h2 class="section-title testi-title">USER <span class="accent">TESTIMONIALS</span></h2>

<svg class="carousel-arrow" style="left:60px" viewBox="0 0 30 30"><path d="M19 6l-9 9 9 9" stroke="#6b7280" stroke-width="2.5" fill="none"/></svg>
<svg class="carousel-arrow" style="left:1110px" viewBox="0 0 30 30"><path d="M11 6l9 9-9 9" stroke="#6b7280" stroke-width="2.5" fill="none"/></svg>

<article class="testi-card" style="left:110px">
  <div class="stars">★★★★★</div>
  <p>The credit report is easy to use, informative and accurate to the date. Helps me to manage my financial well-being.</p>
  <div class="avatar" role="img" aria-label="Customer portrait"></div>
  <div class="testi-name">Liesl Mostert</div>
</article>
<article class="testi-card" style="left:360px">
  <div class="stars">★★★★★</div>
  <p>Their customer support team has been very impressive. The team and knowledge they shared were of great practical use.</p>
  <div class="avatar" role="img" aria-label="Customer portrait"></div>
  <div class="testi-name">Thandi Nkosi</div>
</article>
<article class="testi-card" style="left:610px">
  <div class="stars">★★★★★</div>
  <p>This app is easy to use and efficient, and it gives me a clear view of my credit in one place.</p>
  <div class="avatar" role="img" aria-label="Customer portrait"></div>
  <div class="testi-name">Pieter du Toit</div>
</article>
<article class="testi-card" style="left:860px">
  <div class="stars">★★★★★</div>
  <p>Excellent credit report service. They respond to queries promptly and have a very detailed credit report which is helpful and informative.</p>
  <div class="avatar" role="img" aria-label="Customer portrait"></div>
  <div class="testi-name">Pieter du Toit</div>
</article>

<footer class="site-footer">
  <a class="brand footer-brand" href="#"><span class="brand-dot"></span>Lumen Ledger</a>
  <div class="footer-col" style="left:330px">
    <h4>TERMS</h4>
    General Terms of Use<br>Exclusion of Liability<br>Security Policy<br>Privacy Policy
  </div>
  <div class="footer-col" style="left:540px">
    <h4>PURCHASE</h4>
    Delivery Policy<br>Data Policy<br>Refund Policy<br>Changes and Fees
  </div>
  <div class="footer-col" style="left:740px">
    <h4>QUICK LINKS</h4>
    About Us<br>Articles<br>Contact Us<br>Login
  </div>
  <div class="footer-col" style="left:920px">
    <h4>FOLLOW US</h4>
    <div class="social"><span></span><span></span><span></span><span></span></div>
  </div>
  <div class="pay-methods"><span></span><span></span><span></span><span></span></div>
  <div class="copyright">© All Rights Reserved lumenledger.co.za | NCR Reg. No NCRCB0000</div>
</footer>

</body>
</html>
```